Oil and Gas Exploration and Production company needs a business card design

We need a business card design using our logo and colors in the logo. We want a mainstream design.

```html
<!DOCTYPE html>
<html lang="en">
<head>
<meta charset="utf-8">
<title>Altura Oil &amp; Gas – Business Card</title>
<link rel="stylesheet" href="https://fonts.googleapis.com/css2?family=Arvo:wght@700&family=Open+Sans:wght@400;600;700&display=swap">
<style>
  :root {
    --ink: #111111;
    --gold: #c9962b;
    --paper: #ffffff;
    --text-grey: #555555;
    --faint: #ececec;
    --backdrop: #d9d9d9;
  }
  * { box-sizing: border-box; margin: 0; padding: 0; }
  html, body { width: 1200px; height: 900px; overflow: hidden; }
  body {
    background: var(--backdrop);
    font-family: "Open Sans", Arial, sans-serif;
    position: relative;
  }
  .card {
    position: absolute;
    width: 640px;
    height: 366px;
    background: var(--paper);
    overflow: hidden;
    box-shadow: 0 6px 18px rgba(0,0,0,.18);
  }
  .card--front { left: 80px; top: 70px; }
  .card--back { left: 480px; top: 464px; }

  .brand {
    display: flex;
    align-items: center;
    gap: 12px;
  }
  .brand__dot {
    width: 26px; height: 26px;
    border-radius: 50%;
    background: var(--gold);
    flex: none;
  }
  .brand__name {
    font-family: "Arvo", Georgia, serif;
    font-weight: 700;
    color: var(--ink);
    line-height: 1;
    white-space: nowrap;
  }

  /* front */
  .card--front .brand {
    position: absolute;
    left: 0; right: 0; top: 128px;
    justify-content: center;
  }
  .card--front .brand__name { font-size: 46px; }
  .front__web {
    position: absolute;
    left: 0; right: 0; top: 252px;
    text-align: center;
    font-size: 14px;
    letter-spacing: 6px;
    color: var(--text-grey);
  }

  /* back */
  .back__decor {
    position: absolute;
    left: 30px; top: 180px;
    width: 240px; height: 240px;
    border-radius: 50%;
    background: var(--faint);
  }
  .card--back .brand {
    position: absolute;
    right: 40px; top: 40px;
  }
  .card--back .brand__dot { width: 22px; height: 22px; }
  .card--back .brand__name { font-size: 36px; }
  .holder {
    position: absolute;
    right: 40px; top: 96px;
    text-align: right;
  }
  .holder__name {
    font-weight: 700;
    font-size: 17px;
    color: var(--ink);
    letter-spacing: .5px;
  }
  .holder__title {
    font-size: 13px;
    color: var(--gold);
    font-weight: 600;
  }
  .contact {
    position: absolute;
    right: 40px; top: 168px;
    text-align: right;
    font-size: 13px;
    line-height: 1.6;
    color: var(--text-grey);
  }
  .contact b { color: var(--ink); font-weight: 700; }
  .back__band {
    position: absolute;
    left: 0; right: 0; bottom: 0;
    height: 28px;
    background: var(--ink);
    border-top: 3px solid var(--gold);
  }
  .back__web {
    position: absolute;
    right: 0; bottom: 28px;
    width: 250px; height: 40px;
    background: var(--gold);
    color: var(--paper);
    font-size: 14px;
    letter-spacing: 4px;
    display: flex; align-items: center; justify-content: center;
  }
</style>
</head>
<body>
  <section class="card card--front">
    <div class="brand">
      <span class="brand__dot"></span>
      <span class="brand__name">Altura Oil &amp; Gas</span>
    </div>
    <p class="front__web">www.alturaoilgas.com</p>
  </section>

  <section class="card card--back">
    <div class="back__decor"></div>
    <div class="brand">
      <span class="brand__dot"></span>
      <span class="brand__name">Altura Oil &amp; Gas</span>
    </div>
    <div class="holder">
      <p class="holder__name">ORIN CASTELLANE</p>
      <p class="holder__title">PRESIDENT</p>
    </div>
    <div class="contact">
      <p>4120 Ridgeline Avenue Clearwater, NY 11020</p>
      <p><b>P:</b> 555 0142 2870 <b>M:</b> 555 0176 4391 <b>F:</b> 555 0198 6624</p>
      <p><b>E:</b> info@alturaoilgas.com</p>
    </div>
    <div class="back__web">www.alturaoilgas.com</div>
    <div class="back__band"></div>
  </section>
</body>
</html>
```